Brightmill Data Works

Our company is about IT hardwares and IT solutions. IT hardware such as PC, RAMS, storage and servers. IT solutions such as project management, BA. We are also selling new technology too.

Target Market(s)

Consumer, Small to Medium Business, Corporate

Requirements
Must have
• The business card must have the following:
• Name:
• Title:
• Contact Number:
• Email address:
• Website:
• Color: Must match the logo color upgrade

```html
<!DOCTYPE html>
<html lang="en">
<head>
<meta charset="utf-8">
<title>Brightmill Data Works – Business Card</title>
<link href="https://fonts.googleapis.com/css2?family=Lato:wght@400;700;900&display=swap" rel="stylesheet">
<style>
  :root {
    --backdrop: #161616;
    --card: #262626;
    --card-edge: #2e2e2e;
    --amber: #e39a2d;
    --ink: #f2f2f2;
    --ink-soft: #d9d9d9;
  }
  * { box-sizing: border-box; margin: 0; padding: 0; }
  html, body {
    width: 1200px; height: 912px; overflow: hidden;
    background: var(--backdrop);
    font-family: "Lato", sans-serif;
  }
  .canvas {
    position: relative; width: 1200px; height: 912px;
    display: flex; flex-direction: column; align-items: center; justify-content: center; gap: 40px;
  }
  .card {
    position: relative; width: 680px; height: 389px;
    background: linear-gradient(160deg, var(--card-edge), var(--card));
    box-shadow: 0 14px 30px rgba(0,0,0,.55);
    overflow: hidden;
  }
  /* Wordmark */
  .wordmark { display: flex; align-items: center; gap: 14px; }
  .wordmark__dot { width: 18px; height: 18px; background: var(--amber); }
  .wordmark__name {
    font-weight: 900; color: var(--ink); text-transform: uppercase;
    letter-spacing: 1px; line-height: 1.05;
  }
  /* Front */
  .card--front { display: flex; flex-direction: column; align-items: center; justify-content: center; }
  .card--front .wordmark__name { font-size: 38px; }
  .card--front .site {
    margin-top: 58px; color: var(--ink-soft); font-size: 15px; letter-spacing: .5px;
  }
  /* Back */
  .card--back .brand {
    position: absolute; left: 44px; top: 150px; width: 270px;
  }
  .card--back .wordmark__name { font-size: 26px; }
  .divider {
    position: absolute; left: 336px; top: 80px; width: 1.5px; height: 150px;
    background: var(--amber);
  }
  .contact { position: absolute; left: 372px; top: 70px; }
  .contact__name { color: var(--amber); font-weight: 700; font-size: 24px; }
  .contact__title { color: var(--ink); font-size: 14px; margin: 2px 0 14px; }
  .contact__list { list-style: none; }
  .contact__item {
    display: flex; align-items: center; gap: 10px;
    color: var(--ink); font-size: 15px; line-height: 24px;
  }
  .contact__item svg { width: 15px; height: 15px; fill: var(--amber); flex: none; }
  .address {
    position: absolute; right: 40px; bottom: 34px;
    color: var(--ink); font-size: 17px;
  }
  .base-bar {
    position: absolute; left: 0; right: 0; bottom: 0; height: 8px; background: var(--amber);
  }
</style>
</head>
<body>
<main class="canvas">
  <section class="card card--front" aria-label="Card front">
    <div class="wordmark">
      <span class="wordmark__dot"></span>
      <span class="wordmark__name">Brightmill Data Works</span>
    </div>
    <p class="site">www.brightmilldata.com</p>
  </section>

  <section class="card card--back" aria-label="Card back">
    <div class="brand wordmark">
      <span class="wordmark__dot"></span>
      <span class="wordmark__name">Brightmill<br>Data Works</span>
    </div>
    <span class="divider"></span>
    <div class="contact">
      <p class="contact__name">Daniel Ashford</p>
      <p class="contact__title">Manager</p>
      <ul class="contact__list">
        <li class="contact__item">
          <svg viewBox="0 0 16 16" aria-hidden="true"><path d="M3.6 1.5l2.3 2.6-1.2 1.6c.9 2 2.5 3.6 4.6 4.6l1.6-1.2 2.6 2.3-1.4 2.1C7 13.5 2.5 9 1.5 2.9z"/></svg>
          512 555 0142
        </li>
        <li class="contact__item">
          <svg viewBox="0 0 16 16" aria-hidden="true"><path d="M4 1h8v4H4zM1 6h14v6h-3v3H4v-3H1zm4 4v4h6v-4z"/></svg>
          512 555 0143
        </li>
        <li class="contact__item">
          <svg viewBox="0 0 16 16" aria-hidden="true"><path d="M1 3h14v10H1zm1.5 1.2L8 8.6l5.5-4.4z"/></svg>
          info@brightmilldata.com
        </li>
        <li class="contact__item">
          <svg viewBox="0 0 16 16" aria-hidden="true"><path d="M8 1a7 7 0 100 14A7 7 0 008 1zm0 1.4c.8 0 1.7 1.5 2 3.6H6c.3-2.1 1.2-3.6 2-3.6zM2.5 7h3.4v2H2.5zm4.4 0h2.2v2H6.9zm3.2 0h3.4v2h-3.4zM6 10h4c-.3 2.1-1.2 3.6-2 3.6S6.3 12.1 6 10z"/></svg>
          www.brightmilldata.com
        </li>
      </ul>
    </div>
    <p class="address">418 Alder Court, Houston, TX 77041</p>
    <span class="base-bar"></span>
  </section>
</main>
</body>
</html>
```